Interval Timer App

Need to have design for the attached wireframe. Similar app can be found here: https://shop.lumaverse.net/store/apps/details?id=cc.quillfern.pulseclock

```html
<!DOCTYPE html>
<html lang="en">
<head>
<meta charset="UTF-8">
<title>Interval Timer – Quit Confirmation</title>
<link rel="stylesheet" href="https://fonts.googleapis.com/css2?family=Open+Sans:wght@400;500;600&display=swap">
<style>
  :root {
    --bg-top: #46a09f;
    --bg-bottom: #177aa6;
    --accent: #1a7fe6;
    --accent-dark: #1e6fb5;
    --ink: #1c1c24;
    --ink-soft: #333338;
    --card-dimmed: #9c9ea3;
    --skip-dimmed: #1e5fa5;
    --skip-text: #8ea9c9;
    --white: #ffffff;
  }
  * { box-sizing: border-box; margin: 0; padding: 0; }
  html, body {
    width: 675px;
    height: 1200px;
    overflow: hidden;
  }
  body {
    font-family: "Open Sans", sans-serif;
    background: linear-gradient(170deg, var(--bg-top) 0%, #2f8ea3 50%, var(--bg-bottom) 100%);
    position: relative;
  }
  .screen { position: relative; width: 675px; height: 1200px; }

  .back-button {
    position: absolute;
    left: 30px;
    top: 38px;
    width: 30px;
    height: 36px;
  }

  .set-progress {
    position: absolute;
    left: 199px;
    top: 164px;
    width: 283px;
    text-align: center;
  }
  .set-label {
    font-size: 21px;
    font-weight: 500;
    color: var(--ink);
    letter-spacing: 0.5px;
    line-height: 30px;
  }
  .set-track {
    position: relative;
    margin-top: 8px;
    height: 5px;
    background: var(--white);
    border-radius: 3px;
  }
  .set-track-fill {
    position: absolute;
    left: 0; top: 0;
    width: 120px;
    height: 5px;
    background: var(--accent);
    border-radius: 3px;
  }
  .set-knob {
    position: absolute;
    left: 109px;
    top: -8px;
    width: 21px;
    height: 21px;
    border-radius: 50%;
    background: var(--white);
    border: 3px solid var(--accent);
  }

  .rest-card {
    position: absolute;
    left: 30px;
    top: 281px;
    width: 615px;
    height: 638px;
    background: var(--card-dimmed);
    border-radius: 15px;
  }
  .rest-title {
    position: absolute;
    top: 50px;
    width: 100%;
    text-align: center;
    font-size: 41px;
    font-weight: 500;
    color: #2d2d38;
  }
  .skip-button {
    position: absolute;
    left: 187px;
    top: 533px;
    width: 242px;
    height: 75px;
    border-radius: 38px;
    background: var(--skip-dimmed);
    color: var(--skip-text);
    font-size: 24px;
    font-weight: 500;
    letter-spacing: 1px;
    display: flex;
    align-items: center;
    justify-content: center;
  }

  .quit-dialog {
    position: absolute;
    left: 30px;
    top: 429px;
    width: 615px;
    height: 342px;
    background: var(--white);
    border-radius: 8px;
  }
  .dialog-title {
    position: absolute;
    top: 24px;
    width: 100%;
    text-align: center;
    font-size: 34px;
    font-weight: 500;
    color: var(--ink);
  }
  .dialog-message {
    position: absolute;
    top: 130px;
    width: 100%;
    text-align: center;
    font-size: 30px;
    font-weight: 400;
    color: var(--ink-soft);
  }
  .dialog-button {
    position: absolute;
    top: 248px;
    width: 242px;
    height: 73px;
    border-radius: 37px;
    font-size: 26px;
    letter-spacing: 1px;
    display: flex;
    align-items: center;
    justify-content: center;
  }
  .dialog-button--yes {
    left: 19px;
    border: 3px solid var(--accent);
    color: var(--accent);
    font-weight: 400;
  }
  .dialog-button--no {
    left: 354px;
    background: var(--accent);
    color: var(--white);
    font-weight: 600;
  }
</style>
</head>
<body>
<main class="screen">
  <svg class="back-button" viewBox="0 0 30 36" aria-label="Back">
    <polyline points="22,4 8,18 22,32" fill="none" stroke="var(--accent-dark)" stroke-width="4" stroke-linecap="round" stroke-linejoin="round"/>
  </svg>

  <div class="set-progress">
    <div class="set-label">SET 1</div>
    <div class="set-track">
      <div class="set-track-fill"></div>
      <div class="set-knob"></div>
    </div>
  </div>

  <section class="rest-card">
    <h1 class="rest-title">Rest time!</h1>
    <div class="skip-button">SKIP</div>
  </section>

  <section class="quit-dialog" role="dialog">
    <h2 class="dialog-title">Do you really want to quit?</h2>
    <p class="dialog-message">All your progress will be lost!</p>
    <div class="dialog-button dialog-button--yes">YES</div>
    <div class="dialog-button dialog-button--no">NO</div>
  </section>
</main>
</body>
</html>
```